Dean Hartwell realestate

We want something complete different to our website now and something that will stand out this is our website http://deanhartwellrealestate.com/

our company website for my boss is www.gordonvale.com

please note this website is being made for dean hartwell not gordon vale

something similar to our company website but has to be in the branding of dean hartwell realestate

```html
<!DOCTYPE html>
<html lang="en">
<head>
<meta charset="utf-8">
<title>Dean Hartwell Property</title>
<link href="https://fonts.googleapis.com/css2?family=Montserrat:wght@400;600;700;800&family=Open+Sans:wght@400;600&display=swap" rel="stylesheet">
<style>
:root{
  --orange:#ee5a24;
  --navy:#1d2a47;
  --ink:#2b2b33;
  --muted:#7a7d86;
  --pale:#eeeff2;
  --line:#dcdde2;
  --white:#ffffff;
}
*{box-sizing:border-box;margin:0;padding:0}
html,body{width:1200px;height:3472px;overflow:hidden}
body{font-family:"Open Sans",Arial,sans-serif;color:var(--ink);background:var(--white);position:relative}
.section{position:absolute;left:0;width:1200px}
h1,h2,h3,h4,.nav,.btn{font-family:"Montserrat",Arial,sans-serif}
.btn{display:inline-block;background:var(--orange);color:var(--white);font-weight:700;font-size:15px;letter-spacing:1px;padding:12px 28px;border-radius:3px}

/* hero */
.hero{top:0;height:640px}
.hero-photo{position:absolute;inset:0;background:linear-gradient(180deg,#3d3b6b 0%,#7d6a9a 22%,#c9a98f 38%,#5a4a45 55%,#8b7d74 75%,#5d6a73 100%)}
.hero-shade{position:absolute;inset:0;background:rgba(20,20,40,.25)}
.topbar{position:absolute;top:0;left:0;right:0;height:96px;display:flex;align-items:center;padding:0 128px;justify-content:space-between}
.brand{font-family:"Montserrat",Arial,sans-serif;font-weight:700;color:var(--white);font-size:30px}
.nav{display:flex;align-items:center;gap:10px;font-size:13px;font-weight:600;color:var(--white)}
.nav a{padding:8px 12px;color:var(--white);text-decoration:none}
.nav a.active{background:var(--white);color:var(--navy)}
.nav .dot{width:24px;height:24px;border:2px solid var(--white);border-radius:50%;margin-left:4px}
.slide-arrow{position:absolute;top:300px;width:36px;height:40px;display:flex;align-items:center;justify-content:center}
.hero-copy{position:absolute;top:254px;width:100%;text-align:center;color:var(--white)}
.hero-copy h1{font-size:52px;font-weight:800;letter-spacing:1px}
.hero-copy p{font-family:"Montserrat",Arial,sans-serif;font-size:20px;font-weight:600;letter-spacing:1px;margin:6px 0 24px}
.video{position:absolute;left:392px;top:488px;width:416px;height:192px;border:6px solid var(--white);background:linear-gradient(90deg,#2c3550,#4b5a78 55%,#9a4a35);box-shadow:0 8px 24px rgba(0,0,0,.3);z-index:3}
.video svg{position:absolute;left:168px;top:50px}

/* sold */
.sold{top:640px;height:580px;background:var(--pale)}
.sold h2{position:absolute;top:112px;width:100%;text-align:center;font-size:20px;font-weight:700;letter-spacing:1px}
.rule{display:block;width:44px;height:2px;background:var(--muted);margin:14px auto 0}
.cards{position:absolute;top:228px;left:128px;display:flex;gap:16px}
.card{position:relative;width:224px;height:212px;color:var(--white)}
.card .photo{position:absolute;inset:0}
.card .tag{position:absolute;left:0;top:0;background:var(--orange);font-size:11px;font-weight:700;padding:5px 10px;font-family:"Montserrat",Arial,sans-serif}
.card .addr{position:absolute;left:14px;bottom:14px;font-size:12px;font-weight:600;line-height:1.4;text-transform:uppercase}
.dots{position:absolute;top:500px;width:100%;display:flex;justify-content:center;gap:8px}
.dots span{width:8px;height:8px;border-radius:50%;background:#c9cbd1}
.dots span.on{background:var(--orange)}

/* welcome */
.welcome{top:1220px;height:540px}
.welcome-photo{position:absolute;inset:0;background:linear-gradient(100deg,#16254a 0%,#24386a 38%,#3d4f7c 60%,#6b5a52 80%,#3a3a48 100%)}
.welcome-copy{position:absolute;left:128px;top:100px;width:400px;color:var(--white)}
.welcome-copy h3{font-size:20px;font-weight:700}
.welcome-copy h2{font-size:28px;font-weight:800;margin-bottom:10px}
.welcome-copy p{font-size:13px;line-height:1.55;margin-bottom:22px;color:#e6e9f2}
.welcome .btn{font-size:12px;padding:10px 18px}

/* testimonials */
.clients{top:1760px;height:700px;background:var(--white);overflow:hidden}
.clients .band{position:absolute;inset:0}
.quote-box{position:absolute;left:200px;top:128px;width:792px;height:452px;background:var(--white);box-shadow:0 4px 20px rgba(0,0,0,.12)}
.quote-box h2{text-align:center;font-size:19px;font-weight:700;margin-top:50px;letter-spacing:.5px}
.quote-box .divider{height:1px;background:var(--line);margin:18px 40px 0}
.quotes{display:flex;gap:80px;padding:42px 70px 0}
.quote{flex:1;display:flex;gap:18px}
.quote .mark{font-family:Georgia,serif;font-size:80px;line-height:.8;color:#c4c6cc}
.quote p{font-size:13px;line-height:1.6;color:var(--muted)}
.quote h4{font-size:12px;margin-top:20px}
.quote small{font-size:11px;color:var(--muted)}
.q-arrow{position:absolute;top:362px;width:28px;height:28px;border-radius:50%;background:#3a3d47;display:flex;align-items:center;justify-content:center}

/* appraisal */
.appraisal{top:2460px;height:600px}
.appraisal-photo{position:absolute;inset:0;background:linear-gradient(180deg,#5c6a96 0%,#8a8db0 28%,#6d6660 50%,#4b7d8e 78%,#2d6f9a 100%)}
.appraisal h2{position:absolute;top:54px;width:100%;text-align:center;color:var(--white);font-size:28px;font-weight:700;letter-spacing:1px}
.form{position:absolute;left:352px;top:140px;width:488px;height:380px;background:rgba(255,255,255,.85);padding:20px 16px}
.row{display:flex;gap:12px;margin-bottom:12px}
.field{flex:1;height:30px;background:var(--white);border:1px solid var(--line);font-size:11px;color:var(--muted);padding:7px 10px}
.field.tall{height:110px}
.form .btn{position:absolute;left:50%;transform:translateX(-50%);bottom:28px;font-size:14px;padding:10px 24px}

/* footer */
.footer{top:3060px;height:412px;background:var(--white)}
.col{position:absolute;top:56px}
.col h4{font-size:12px;font-weight:700;margin-bottom:16px;letter-spacing:.5px}
.col li{list-style:none;font-size:11px;color:var(--ink);display:flex;align-items:center;gap:12px;margin-bottom:14px}
.col .ic{width:22px;height:22px;border-radius:50%;background:var(--orange)}
.menu li{margin-bottom:6px;text-transform:uppercase}
.map{position:absolute;left:720px;top:80px;width:352px;height:210px;background:linear-gradient(135deg,#e9e6df,#d8dfe5 60%,#f1e4c9)}
.foot-rule{position:absolute;left:128px;right:128px;top:300px;height:1px;background:var(--line)}
.foot-brand{position:absolute;left:128px;top:308px;font-family:"Montserrat",Arial,sans-serif;font-weight:700;color:#1e3a8a;font-size:24px}
.legal{position:absolute;right:128px;top:320px;text-align:right;font-size:10px;color:var(--muted);line-height:1.6}
</style>
</head>
<body>

<header class="section hero">
  <div class="hero-photo" role="img" aria-label="Evening photo of a home with a pergola patio beside a lit swimming pool"></div>
  <div class="hero-shade"></div>
  <div class="topbar">
    <div class="brand">Dean Hartwell Property</div>
    <nav class="nav">
      <a class="active">HOME</a><a>PORTFOLIO</a><a>AGENTS</a><a>BOOK APPRAISAL</a><a>CONTACT</a>
      <span class="dot"></span><span class="dot"></span>
    </nav>
  </div>
  <div class="slide-arrow" style="left:8px"><svg width="14" height="24"><path d="M12 2 2 12l10 10" stroke="#fff" stroke-width="3" fill="none"/></svg></div>
  <div class="slide-arrow" style="right:8px"><svg width="14" height="24"><path d="M2 2l10 10L2 22" stroke="#fff" stroke-width="3" fill="none"/></svg></div>
  <div class="hero-copy">
    <h1>REAL ESTATE HARTWELL</h1>
    <p>TRUST, CONFIDENCE AND INTEGRITY</p>
    <span class="btn">READ MORE</span>
  </div>
  <div class="video" role="img" aria-label="Video still of the agent standing in front of a property">
    <svg width="68" height="68" viewBox="0 0 68 68"><circle cx="34" cy="34" r="32" fill="#fff"/><path d="M27 21l20 13-20 13z" fill="#1d2a47"/></svg>
  </div>
</header>

<section class="section sold">
  <h2>LATEST PROPERTIES SOLD<span class="rule"></span></h2>
  <div class="cards">
    <div class="card"><div class="photo" role="img" aria-label="Brick house with tiled roof under blue sky" style="background:linear-gradient(180deg,#4f79b8,#9b5f4a 60%,#6d6a5d)"></div><span class="tag">SOLD</span><div class="addr">14 Marlow Street<br>Kelvale 6105</div></div>
    <div class="card"><div class="photo" role="img" aria-label="Modern home front with garden at dusk" style="background:linear-gradient(180deg,#2f3c52,#6d6458 55%,#3f4a3a)"></div><span class="tag">SOLD</span><div class="addr">8 Ferndale Court<br>Leighton 6025</div></div>
    <div class="card"><div class="photo" role="img" aria-label="Double storey house with garage and driveway" style="background:linear-gradient(180deg,#5c86c2,#a07a60 60%,#7a7268)"></div><span class="tag">SOLD</span><div class="addr">22 Aspen Avenue<br>Lynwood 6147</div></div>
    <div class="card"><div class="photo" role="img" aria-label="Single storey brick home with lawn" style="background:linear-gradient(180deg,#4a74b0,#8e5546 60%,#5f6a4b)"></div><span class="tag">SOLD</span><div class="addr">5 Wattle Street<br>Kelvale 6105</div></div>
  </div>
  <div class="dots"><span class="on"></span><span></span><span></span><span></span></div>
</section>

<section class="section welcome">
  <div class="welcome-photo" role="img" aria-label="Agent in a suit standing before a brick home under an evening sky"></div>
  <div class="welcome-copy">
    <h3>WELCOME TO</h3>
    <h2>DEAN HARTWELL PROPERTY</h2>
    <p>Raised in the local area, Dean has built his career on hard work, honest advice and a genuine care for every client. His local knowledge and tireless approach help owners achieve outstanding results for their homes.</p>
    <span class="btn">READ MORE</span>
  </div>
</section>

<section class="section clients">
  <svg class="band" width="1200" height="700" aria-hidden="true"><polygon points="640,0 1200,0 1200,700 300,700" fill="#eeeff2"/></svg>
  <div class="quote-box">
    <h2>WHAT OUR CLIENTS THINK<span class="rule"></span></h2>
    <div class="divider"></div>
    <div class="quotes">
      <div class="quote"><span class="mark">&ldquo;</span><div><p>We bought our first home through Dean and the process was easy and stress free. He kept us informed at every step and his honest advice helped us feel confident. We would happily recommend him to friends and family.</p><h4>SARAH M. ELLIS</h4><small>Kelvale, 2018</small></div></div>
      <div class="quote"><span class="mark">&ldquo;</span><div><p>I found Dean to be different from most agents in that he listened and was always ready to help. His market knowledge secured a great price and I would use him again.</p><h4>TOM R.</h4><small>Lynwood, 2018</small></div></div>
    </div>
  </div>
  <div class="q-arrow" style="left:186px"><svg width="10" height="12"><path d="M8 1 2 6l6 5" stroke="#fff" stroke-width="2" fill="none"/></svg></div>
  <div class="q-arrow" style="left:978px"><svg width="10" height="12"><path d="M2 1l6 5-6 5" stroke="#fff" stroke-width="2" fill="none"/></svg></div>
</section>

<section class="section appraisal">
  <div class="appraisal-photo" role="img" aria-label="Backyard with swimming pool, palms and fence at dusk"></div>
  <h2>BOOK AN APPRAISAL</h2>
  <div class="form">
    <div class="row"><div class="field">Name</div><div class="field">Email</div></div>
    <div class="row"><div class="field">Phone</div><div class="field">Preferred Date</div></div>
    <div class="row"><div class="field">Address</div></div>
    <div class="row"><div class="field tall">Message</div></div>
    <span class="btn">BOOK NOW</span>
  </div>
</section>

<footer class="section footer">
  <div class="col" style="left:128px">
    <h4>CONNECT WITH US</h4>
    <ul><li><span class="ic"></span>Social Feed</li><li><span class="ic"></span>Updates</li><li><span class="ic"></span>Network</li></ul>
  </div>
  <div class="col" style="left:328px">
    <h4>CONTACT US</h4>
    <ul>
      <li><svg width="16" height="20" viewBox="0 0 16 20"><path d="M8 1a6 6 0 0 0-6 6c0 5 6 12 6 12s6-7 6-12a6 6 0 0 0-6-6z" fill="#ee5a24"/><circle cx="8" cy="7" r="2.2" fill="#fff"/></svg>Suite 4, 18 Larchmont Road<br>Bayview WA 6152 Australia</li>
      <li><svg width="16" height="16" viewBox="0 0 16 16"><path d="M3 1l3 3-2 2c1 2 3 4 5 5l2-2 3 3-2 3C7 15 1 9 1 3z" fill="#ee5a24"/></svg>08 9412 5580</li>
      <li><svg width="16" height="12" viewBox="0 0 16 12"><rect x="1" y="1" width="14" height="10" fill="none" stroke="#ee5a24" stroke-width="1.6"/><path d="M1 1l7 6 7-6" fill="none" stroke="#ee5a24" stroke-width="1.6"/></svg>hello@deanhartwell.com</li>
    </ul>
  </div>
  <div class="col menu" style="left:580px">
    <h4>MENU</h4>
    <ul><li>Home</li><li>Portfolio</li><li>Agents</li><li>Book Appraisal</li><li>Contact</li></ul>
  </div>
  <div class="map" role="img" aria-label="Street map showing the office location"></div>
  <div class="foot-rule"></div>
  <div class="foot-brand">Dean Hartwell Property</div>
  <div class="legal">Sitemap | Privacy<br>Copyright © 2018 All Rights Reserved</div>
</footer>

</body>
</html>
```